Tolbek cards

I want a simple business card that pops.
Logo on one side.
On side two i want.
"Are you thinking about a new building on your property, or renovating an existing structure? Contact".....
Owners Name: Dale Whitacre
Owners Phone number: 610-555-0187
Address:4076 Copper Ridge RD, Millbrook, PA 17520
Committed to Quality, Service, and Integrity

```html
<!DOCTYPE html>
<html lang="en">
<head>
<meta charset="utf-8">
<title>Tolbek Builders LLC – Business Card</title>
<link href="https://fonts.googleapis.com/css2?family=Roboto:wght@300;400;700&display=swap" rel="stylesheet">
<style>
  :root {
    --page-bg: #e9e5e0;
    --card-bg: #efebe6;
    --panel-dark: #67564b;
    --panel-edge: #8b7767;
    --ink-dark: #4a3b32;
    --ink-taupe: #8a7563;
    --ink-body: #4f423a;
    --band-bg: #7b6757;
    --band-text: #e7ddd3;
    --rule: #a89888;
    --white: #ffffff;
  }
  * { margin: 0; padding: 0; box-sizing: border-box; }
  html, body {
    width: 1200px;
    height: 1054px;
    overflow: hidden;
    background: var(--page-bg);
    font-family: "Roboto", Arial, sans-serif;
  }
  .card {
    position: absolute;
    left: 100px;
    top: 227px;
    width: 1000px;
    height: 600px;
    border-radius: 28px;
    overflow: hidden;
    background: var(--card-bg);
    box-shadow: 0 18px 40px rgba(60, 45, 35, 0.18);
  }
  .card-shapes {
    position: absolute;
    inset: 0;
  }
  .pitch {
    position: absolute;
    left: 90px;
    top: 96px;
    width: 245px;
    color: var(--white);
    font-size: 33px;
    line-height: 52px;
    font-weight: 300;
  }
  .contact-label {
    position: absolute;
    left: 517px;
    top: 99px;
    width: 426px;
    display: flex;
    align-items: center;
    gap: 10px;
    font-size: 17px;
    color: var(--ink-body);
  }
  .contact-label::after {
    content: "";
    flex: 1;
    height: 1px;
    background: var(--rule);
  }
  .brand {
    position: absolute;
    left: 517px;
    top: 156px;
    display: flex;
    align-items: center;
    gap: 20px;
  }
  .brand-mark {
    width: 62px;
    height: 62px;
    background: var(--ink-dark);
  }
  .brand-name {
    display: flex;
    flex-direction: column;
    font-weight: 700;
    color: var(--ink-dark);
    text-transform: uppercase;
  }
  .brand-name .word {
    font-size: 54px;
    line-height: 50px;
    letter-spacing: 0.5px;
  }
  .brand-name .suffix {
    font-size: 19px;
    line-height: 22px;
    letter-spacing: 6.4px;
  }
  .owner-name {
    position: absolute;
    left: 517px;
    top: 283px;
    font-size: 38px;
    font-weight: 700;
    letter-spacing: 0.5px;
    color: var(--ink-dark);
  }
  .owner-name .surname { color: var(--ink-taupe); }
  .details {
    position: absolute;
    left: 517px;
    top: 336px;
    list-style: none;
    font-size: 24px;
    line-height: 32px;
    color: var(--ink-body);
  }
  .details li {
    display: flex;
    align-items: flex-start;
    gap: 12px;
    margin-bottom: 8px;
  }
  .details svg { flex: none; margin-top: 5px; }
  .tagline {
    position: absolute;
    right: 55px;
    top: 527px;
    font-size: 21px;
    color: var(--band-text);
  }
</style>
</head>
<body>
  <div class="card">
    <svg class="card-shapes" width="1000" height="600" viewBox="0 0 1000 600" aria-hidden="true">
      <rect class="band" x="300" y="516" width="700" height="50" fill="var(--band-bg)" opacity="0.85"/>
      <path class="panel-edge" d="M0 0 H420 C478 160 488 420 362 600 H0 Z" fill="var(--panel-edge)"/>
      <path class="panel" d="M0 0 H405 C460 160 470 420 345 600 H0 Z" fill="var(--panel-dark)"/>
    </svg>

    <p class="pitch">Are you thinking about a new building on your property, or renovating an existing structure?</p>

    <div class="contact-label">Contact:</div>

    <div class="brand">
      <span class="brand-mark"></span>
      <span class="brand-name">
        <span class="word">Tolbek</span>
        <span class="suffix">Builders LLC</span>
      </span>
    </div>

    <h1 class="owner-name">DALE <span class="surname">WHITACRE</span></h1>

    <ul class="details">
      <li class="phone">
        <svg width="20" height="20" viewBox="0 0 24 24" fill="none" stroke="var(--ink-body)" stroke-width="1.8">
          <circle cx="12" cy="12" r="10.5"/>
          <path d="M8.5 7.2c-.6.4-1 1.1-.9 1.9.4 3.2 3.1 5.9 6.3 6.3.8.1 1.5-.3 1.9-.9l-1.8-1.6-1.2.7c-1.2-.5-2.2-1.5-2.7-2.7l.7-1.2z"/>
        </svg>
        <span>610-555-0187</span>
      </li>
      <li class="address">
        <svg width="20" height="22" viewBox="0 0 24 26" fill="none" stroke="var(--ink-body)" stroke-width="1.8">
          <path d="M12 24s-8-8.2-8-14a8 8 0 0 1 16 0c0 5.8-8 14-8 14z"/>
          <circle cx="12" cy="10" r="3"/>
        </svg>
        <span>4076 Copper Ridge RD,<br>Millbrook, PA 17520</span>
      </li>
    </ul>

    <p class="tagline">Committed to Quality, Service &amp; Integrity</p>
  </div>
</body>
</html>
```